Industrial Company Profile Brochure Design

We need company profile brochure design. We are in industrial valve business and we are serving oil, petrochemical and power plants. We are working with our clients as trusted advisor. So, the final design should communicate valve solutions expert. The brochure should be 4 pages (including front and back) or folded style. However, it is open. We do not like to put any restriction on creativity. We leave the decision for number of pages and page size to the designer. The color theme should be same as / compatible with logo colors. You should use icons.Find attached the followings:- Our Logo- Word file that contains the required content (text and photos) for the brochure.3 Modern brochure designs. We like these designs. This is just to give you idea about what we like. The brochure is simple, clear and easy to get full information quickly.- Just banner for valve and components. You may need it.

Target Market(s)

The end users of oi, petrochemical and power plants

Industry/Entity Type

Engineering Consulting

Requirements
Must have
• - You must add our slogan. It is "Your Valves Solutions Expert"

```html
<!DOCTYPE html>
<html lang="en">
<head>
<meta charset="utf-8">
<title>Korvan Ridge – Company Profile Brochure</title>
<link rel="stylesheet" href="https://fonts.googleapis.com/css2?family=Montserrat:wght@400;500;600;700;800&family=Oswald:wght@500;600;700&display=swap">
<style>
  :root{
    --orange:#f7870f;
    --orange-deep:#ee7d05;
    --slate:#8c9598;
    --slate-dark:#7d8588;
    --ink:#2b2b2b;
    --white:#ffffff;
    --band:#e3e6e6;
    --photo-dark:#3a3c3e;
  }
  *{margin:0;padding:0;box-sizing:border-box}
  html,body{width:1200px;height:488px;overflow:hidden;background:var(--white)}
  body{font-family:"Montserrat",sans-serif;color:var(--white)}
  .board{position:relative;width:1200px;height:488px;background:linear-gradient(var(--white) 0 331px,var(--band) 331px)}
  .side-title{position:absolute;top:26px;font-family:"Oswald",sans-serif;font-weight:700;font-size:34px;letter-spacing:2px;color:var(--orange);transform:translateX(-50%)}
  .side-title.front{left:317px}
  .side-title.back{left:884px}

  .sheet{position:absolute;top:81px;width:517px;height:366px;box-shadow:0 2px 5px rgba(0,0,0,.25);overflow:hidden}
  .sheet.front{left:59px}
  .sheet.back{left:625px}
  .abs{position:absolute}

  .heading{font-family:"Oswald",sans-serif;font-weight:500;font-size:8.5px;letter-spacing:.4px;line-height:1;border-left:1.5px solid currentColor;padding-left:4px}
  .sub{font-weight:500;font-size:5.6px;line-height:1}
  .copy{font-size:3.9px;line-height:5.2px;font-weight:400}
  .copy p+p{margin-top:4px}
  .bullets{list-style:disc;padding-left:6px;font-size:3.9px;line-height:7px}
  .photo{border:1.5px solid var(--white)}

  /* front */
  .front-panel{left:0;top:0;width:258px;height:278px;background:var(--orange)}
  .front-footer{left:0;top:278px;width:258px;height:88px;background:var(--slate)}
  .cover-photo{left:258px;top:0;width:259px;height:366px;background:
      radial-gradient(ellipse 60% 40% at 55% 45%,rgba(247,150,60,.75),rgba(210,120,110,.35) 55%,transparent 75%),
      linear-gradient(180deg,#4a4c4e 0%,#6b6e70 35%,#3b3d3f 70%,#1f2122 100%)}
  .cover-name{left:258px;width:259px;top:284px;text-align:center;font-weight:800;color:var(--orange);font-size:27px;line-height:27px;letter-spacing:.5px}
  .cover-slogan{left:258px;width:259px;top:342px;text-align:center;font-weight:600;color:var(--white);font-size:6.5px;letter-spacing:1.2px;text-transform:uppercase}
  .feature-icon{width:14px;height:14px;border-radius:50%;background:rgba(255,255,255,.35);display:flex;align-items:center;justify-content:center}
  .badge{width:50px;height:26px;background:var(--white)}
  .contact-line{display:flex;align-items:center;gap:4px;font-size:4.2px;height:9px}
  .contact-line svg{width:5px;height:5px}
  .mini-name{font-weight:700;font-size:5px;color:var(--white)}

  /* back */
  .strip{left:0;top:0;width:517px;height:86px;background:linear-gradient(90deg,#c9ced2 0%,#e8eaec 30%,#d4d8da 55%,#a9b0b6 75%,#8e9aa8 100%);border-bottom:2px solid #2d2f31}
  .back-left{left:0;top:86px;width:258px;height:271px;background:var(--slate)}
  .back-left-edge{left:0;top:357px;width:258px;height:9px;background:var(--orange)}
  .back-right{left:258px;top:86px;width:259px;height:271px;background:var(--orange)}
  .back-right-edge{left:258px;top:357px;width:259px;height:9px;background:var(--slate)}
  .seal{left:207px;top:178px;width:102px;height:102px;border-radius:50%;background:var(--white);border:4px solid #f3c08b;display:flex;align-items:center;justify-content:center;text-align:center;color:var(--orange);font-weight:800;font-size:13px;line-height:14px}
  .value-icon{width:15px;height:15px;border-radius:50%;background:var(--orange);display:flex;align-items:center;justify-content:center}
  .product{background:#e9ecee;border:1.5px solid var(--white)}
</style>
</head>
<body>
<main class="board">
  <h1 class="side-title front">FRONT SIDE</h1>
  <h1 class="side-title back">BACK SIDE</h1>

  <section class="sheet front">
    <div class="abs front-panel"></div>

    <h3 class="abs sub" style="left:10px;top:17px">Spare Parts</h3>
    <div class="abs copy" style="left:10px;top:27px;width:152px">
      <p>We are not only focus on providing reliable valves and upgrades, but also assist our clients in maintaining their valves. We provide direct OEM part replacements, with quality same as those originally installed. Other than providing common spare parts, we can also help in the replacement of obsolete parts not commonly available by using our trusted sources or our highly advanced reverse engineering techniques.</p>
      <p>The advantages of using spare parts provided by us are as follows:</p>
    </div>
    <ul class="abs bullets" style="left:10px;top:73px">
      <li>Completely interchangeable</li>
      <li>Use of latest technology makes our parts highly reliable</li>
      <li>Lower costs</li>
      <li>Faster delivery</li>
    </ul>
    <div class="abs photo" role="img" aria-label="Machined brass valve spare part" style="left:171px;top:10px;width:66px;height:64px;background:linear-gradient(135deg,#c9c2a0,#6f6448 60%,#a99d75)"></div>
    <div class="abs photo" role="img" aria-label="Steel valve stem and bushing parts" style="left:171px;top:81px;width:66px;height:47px;background:linear-gradient(135deg,#d7dadc,#8d9296 60%,#c3c7ca)"></div>

    <h2 class="abs heading" style="left:10px;top:139px">WHY US</h2>
    <p class="abs copy" style="left:10px;top:154px;width:225px">Korvan Ridge offers a full range of consultation services to help analyze your plant requirements for the effective implementation of solutions from our range of products. We cooperate with the end-user for a detailed analysis of the root cause and provide reliable solutions for different kinds of valve problems. Our products and services could be briefly divided into the following sections:</p>

    <div class="abs feature-icon" style="left:10px;top:183px"><svg width="7" height="7" viewBox="0 0 10 10"><rect x="2" y="1" width="6" height="8" fill="none" stroke="#fff" stroke-width="1"/><path d="M3.5 4h3M3.5 6h3" stroke="#fff" stroke-width=".8"/></svg></div>
    <h3 class="abs sub" style="left:30px;top:183px">Quality Control</h3>
    <p class="abs copy" style="left:30px;top:191px;width:205px">Our quality control processes, implemented across all stages of valve solutions development, help in keeping our solutions highly reliable and accurate for long-term implementations.</p>

    <div class="abs feature-icon" style="left:10px;top:209px"><svg width="7" height="7" viewBox="0 0 10 10"><circle cx="5" cy="3.2" r="1.8" fill="#fff"/><path d="M1.5 9c0-2.2 1.6-3.5 3.5-3.5S8.5 6.8 8.5 9z" fill="#fff"/></svg></div>
    <h3 class="abs sub" style="left:30px;top:209px">Customer Satisfaction</h3>
    <p class="abs copy" style="left:30px;top:217px;width:210px">Our teams are committed to handling the needs of our customers in a timely manner, keeping them satisfied and happy. This also makes us a reliable choice for any kind of upgrade or replacement parts in an emergency situation.</p>

    <div class="abs feature-icon" style="left:10px;top:240px"><svg width="7" height="7" viewBox="0 0 10 10"><path d="M1 7l3-3 2 2 3-4" fill="none" stroke="#fff" stroke-width="1.1"/></svg></div>
    <h3 class="abs sub" style="left:30px;top:240px">Highly Affordable</h3>
    <p class="abs copy" style="left:30px;top:249px;width:205px">Our awareness of the latest technologies and unique methods assists us in providing solutions with lower costs; we make sure to pass on this advantage to our clients by keeping our services highly affordable for them.</p>

    <div class="abs front-footer"></div>
    <h2 class="abs heading" style="left:10px;top:290px">PARTNERS</h2>
    <div class="abs badge" style="left:10px;top:302px"></div>
    <div class="abs badge" style="left:63px;top:302px"></div>
    <div class="abs badge" style="left:10px;top:330px"></div>
    <div class="abs badge" style="left:63px;top:330px"></div>

    <h2 class="abs heading" style="left:134px;top:290px">CONTACT DETAILS</h2>
    <p class="abs" style="left:134px;top:304px;font-size:5px;font-weight:500">Korvan Ridge</p>
    <div class="abs" style="left:134px;top:312px">
      <div class="contact-line"><svg viewBox="0 0 10 10"><path d="M2 1l2 2-1 1.5c.8 1.5 1.8 2.5 3.3 3.3L7.8 6.8l2 2L8.5 10C4.5 9.5.5 5.5 0 1.5z" fill="#fff"/></svg>+966 500 123 456</div>
      <div class="contact-line"><svg viewBox="0 0 10 10"><path d="M5 0a3.5 3.5 0 013.5 3.5C8.5 6 5 10 5 10S1.5 6 1.5 3.5A3.5 3.5 0 015 0z" fill="#fff"/><circle cx="5" cy="3.5" r="1.2" fill="#8c9598"/></svg>Harbor Rd - Coastline, 10420</div>
      <div class="contact-line"><svg viewBox="0 0 10 10"><rect x="0.5" y="2" width="9" height="6" fill="#fff"/><path d="M.5 2l4.5 3.5L9.5 2" fill="none" stroke="#8c9598" stroke-width=".8"/></svg>info@korvanridge.example</div>
      <div class="contact-line"><svg viewBox="0 0 10 10"><circle cx="5" cy="5" r="4.3" fill="none" stroke="#fff" stroke-width="1"/><path d="M.7 5h8.6M5 .7c-2.4 2.6-2.4 6 0 8.6M5 .7c2.4 2.6 2.4 6 0 8.6" fill="none" stroke="#fff" stroke-width=".7"/></svg>www.korvanridge.example</div>
    </div>
    <p class="abs mini-name" style="left:214px;top:340px">Korvan Ridge</p>

    <div class="abs cover-photo" role="img" aria-label="Refinery tower at dusk under an orange and violet sky"></div>
    <p class="abs cover-name">KORVAN<br>RIDGE</p>
    <p class="abs cover-slogan">Your Valves Solutions Expert</p>
  </section>

  <section class="sheet back">
    <div class="abs strip" role="img" aria-label="Close-up banner of valve components: cage rings, perforated trims and a valve body"></div>

    <div class="abs back-left"></div>
    <div class="abs back-left-edge"></div>
    <div class="abs back-right"></div>
    <div class="abs back-right-edge"></div>

    <h2 class="abs heading" style="left:10px;top:106px">ABOUT US</h2>
    <div class="abs copy" style="left:10px;top:119px;width:222px">
      <p>Korvan Ridge was established to provide highly-reliable consultation services for a selection of valve designs for various industrial applications. We specialize in recommending new valves for different types of industrial needs, as well as re-engineering the obsolete and troublesome ones, to provide technologically-advanced replacements.</p>
      <p>The key to the company's success is the maintenance of a close working relationship with the clients. This is accomplished by ensuring the best possible solutions for their needs in order to establish and maintain a thorough knowledge and understanding of clients' objectives, helping maximize the benefits.</p>
      <p>We at Korvan Ridge are a group of enthusiastic professionals who take pride in providing quality products to our clients. We help them find the best solutions for their needs by providing highly-experienced consultation services.</p>
    </div>

    <h2 class="abs heading" style="left:10px;top:193px">COMPANY VALUES</h2>
    <p class="abs copy" style="left:10px;top:206px;width:180px">At Korvan Ridge, we are committed to providing the best solutions to our clients and improving our skillsets and technology to deliver high-quality valves and valve components.</p>

    <div class="abs value-icon" style="left:10px;top:228px"><svg width="8" height="8" viewBox="0 0 10 10"><path d="M.5 5C2 2.5 3.5 1.8 5 1.8S8 2.5 9.5 5C8 7.5 6.5 8.2 5 8.2S2 7.5.5 5z" fill="none" stroke="#fff" stroke-width=".9"/><circle cx="5" cy="5" r="1.4" fill="#fff"/></svg></div>
    <h3 class="abs sub" style="left:31px;top:228px">Our Vision</h3>
    <p class="abs copy" style="left:31px;top:237px;width:170px">To become the most trusted valve advisor in the region, maintaining the integrity and reliability of our services among our clients.</p>

    <div class="abs value-icon" style="left:10px;top:253px"><svg width="8" height="8" viewBox="0 0 10 10"><path d="M5 1L1.5 9h7z" fill="none" stroke="#fff" stroke-width=".9"/><path d="M5 1V.2" stroke="#fff" stroke-width=".9"/></svg></div>
    <h3 class="abs sub" style="left:31px;top:254px">Our Mission</h3>
    <p class="abs copy" style="left:31px;top:263px;width:160px">To cooperate with our clients in finding the most reliable and cost-effective solutions for their valve-related requirements.</p>

    <h2 class="abs heading" style="left:10px;top:285px">STRATEGIC APPROACH</h2>
    <div class="abs copy" style="left:10px;top:298px;width:230px">
      <p>The most important aspect of the solutions provided by us is that we deliver tailor-fit designs to accurately and effectively meet the needs that are not well-served by the valves currently available in the market. As in current valve manufacturing companies, the engineers are limited to providing standard designs created by their companies. This also limits them from fulfilling any type of modification requirement. For this reason, there are many valve problems that cannot be solved by standard designs. Furthermore, the parts replacements provided by us meet the requirements and come at a much lower cost, as compared to the parts delivered by these manufacturers.</p>
      <p>We are open and cooperate with several trusted companies to find the best solutions for the end-user problems by providing detailed analysis and consultation services, helping them to buy the most relevant products as per their needs. We aim to be the best choice in valve consultation.</p>
    </div>

    <h2 class="abs heading" style="left:279px;top:106px">OUR SOLUTIONS</h2>
    <p class="abs copy" style="left:279px;top:119px;width:225px">Korvan Ridge offers a full range of consultation services to help analyze your plant requirements for the effective implementation of solutions from our range of products. We cooperate with the end-user for a detailed analysis of the root cause and provide reliable solutions for different kinds of valve problems. Our products and services could be briefly divided into the following sections:</p>

    <h3 class="abs sub" style="left:319px;top:153px">New Valves</h3>
    <p class="abs copy" style="left:319px;top:162px;width:102px">We provide consultation on and design of a variety of valves for different kinds of industrial applications. We have a rich set of valve designs and solutions available, providing solutions for severe service applications. For special valve solutions not available in the market, we can help our clients by manufacturing and delivering those valves in the shortest possible timeframe under the most complicated requirements.</p>
    <div class="abs product" role="img" aria-label="Control valve with red actuator in a workshop" style="left:429px;top:145px;width:66px;height:82px;background:linear-gradient(180deg,#e9ecef 0%,#c3c9ce 40%,#5d6870 100%)"></div>

    <h3 class="abs sub" style="left:319px;top:248px">Upgrade&amp; Retrofit</h3>
    <p class="abs copy" style="left:319px;top:258px;width:102px">We supply highly reliable and efficient upgrading solutions for our clients, with the following key advantages:</p>
    <ul class="abs bullets" style="left:319px;top:274px">
      <li>Fits well into the existing valve</li>
      <li>Full responsibility of the valve</li>
      <li>Detailed documentation</li>
      <li>Saves the cost of piping modifications</li>
      <li>Lower installation costs</li>
      <li>Shorter plant downtime</li>
    </ul>
    <div class="abs product" role="img" aria-label="Compressor valve unloader assembly" style="left:429px;top:240px;width:66px;height:40px"></div>
    <div class="abs product" role="img" aria-label="Yellow actuator cylinder on a valve stem" style="left:429px;top:284px;width:66px;height:67px;background:linear-gradient(180deg,#f4f5f6,#e2d8a8 45%,#eceff1)"></div>
    <div class="abs product" role="img" aria-label="Row of valve internals: poppets, stem and ring plates" style="left:319px;top:322px;width:106px;height:29px;background:#f6f7f8"></div>

    <div class="abs seal">KORVAN<br>RIDGE</div>
  </section>
</main>
</body>
</html>
```